Business Card Design for BrightvaleMedia.com

--I need a business card design for my company BrightvaleMedia.com

I have attached my logo...I want the brightvale media logo on the front of the business card, and then I want The Quillstone Chief on the back of it with my information.

I would like to see a light colored background as well as a dark colored background

FRONT:
BRIGHTVALE MEDIA LOGO
248 N. Larkmoor
3rd Floor
San Diego CA 92173
www.BrightvaleMedia.com

Advanced Website & App Development
Websites, Apps, Online Voucher Systems

Leading Edge Marketing Services
SMS, VB, SMM, SEM,

BACK:
QUILLSTONE CHIEF LOGO
Dorian Pelletta
The Quillstone Chief
Call Or Text: 619-555-0148
Dorian@QuillstoneChief.example
www.QuillstoneChief.example

Target Market(s)

small business owners

Industry/Entity Type

Business Consultant

Contact Information for Business Card

FRONT:
BRIGHTVALE MEDIA LOGO
248 N. Larkmoor
3rd Floor
San Diego CA 92173
www.BrightvaleMedia.com

SMS, VB, SMM, SEM,

BACK:
QUILLSTONE CHIEF LOGO
Dorian Pelletta
The Quillstone Chief
Dorian@QuillstoneChief.example
www.QuillstoneChief.example

Requirements
Must have
• add this quote on it somewhere, anywhere,preferrably on back
• "The Fastest Way To Success Is To Take Action”
• — Dorian Pelletta, Quillstone Chief
Nice to have
• open
Should not have
• red

```html
<!DOCTYPE html>
<html lang="en">
<head>
<meta charset="utf-8">
<title>Brightvale Media – Business Cards</title>
<link rel="stylesheet" href="https://fonts.googleapis.com/css2?family=Lato:wght@400;700;900&display=swap">
<style>
  :root {
    --backdrop: #1c1c1e;
    --card-light: #f7f8fa;
    --card-dark: #2b2b2d;
    --brand-blue: #1577b8;
    --brand-blue-bright: #1e8fd6;
    --text-grey: #5b5f66;
    --text-light: #e9e9ea;
    --rule-grey: #8a8d92;
    --map-light: #dfe3ec;
    --map-dark: #353538;
  }
  * { box-sizing: border-box; margin: 0; padding: 0; }
  html, body {
    width: 1200px; height: 873px; overflow: hidden;
    background: var(--backdrop);
    font-family: "Lato", Arial, sans-serif;
  }
  .stage {
    position: relative; width: 1200px; height: 873px;
    display: flex; align-items: center; justify-content: center; gap: 40px;
  }
  .card {
    position: relative; width: 540px; height: 309px; overflow: hidden;
    box-shadow: 0 10px 30px rgba(0,0,0,.5);
  }

  /* ---------- Light card: personal side ---------- */
  .card--light { background: var(--card-light); }
  .card--light .world-map {
    position: absolute; left: 40px; top: 30px; width: 420px; height: 200px;
    background: radial-gradient(ellipse at 50% 45%, var(--map-light) 0%, rgba(223,227,236,0) 70%);
  }
  .card--light .wordmark {
    position: absolute; right: 40px; top: 46px;
    font-size: 34px; font-weight: 700; letter-spacing: 3px;
    color: var(--brand-blue);
  }
  .identity {
    position: absolute; left: 40px; top: 150px; width: 200px; text-align: right;
  }
  .identity .name { font-size: 19px; font-weight: 700; color: var(--brand-blue); }
  .identity .title { font-size: 15px; color: var(--text-grey); margin-top: 2px; }
  .divider {
    position: absolute; left: 262px; top: 120px; width: 2px; height: 110px;
    background: linear-gradient(to bottom, rgba(138,141,146,0), var(--rule-grey) 40%, rgba(138,141,146,0));
  }
  .contacts {
    position: absolute; left: 282px; top: 126px; list-style: none;
    font-size: 13px; color: var(--text-grey);
  }
  .contacts li { display: flex; align-items: center; gap: 9px; height: 24px; }
  .contacts svg { width: 14px; height: 14px; fill: var(--text-grey); flex: none; }
  .quote-band {
    position: absolute; left: 0; right: 0; bottom: 0; height: 40px;
    background: var(--brand-blue);
    display: flex; align-items: center; justify-content: center;
    color: #fff; font-size: 15px; font-weight: 700; letter-spacing: .3px;
  }

  /* ---------- Dark card: company side ---------- */
  .card--dark { background: var(--card-dark); text-align: center; }
  .card--dark .world-map {
    position: absolute; left: 60px; top: 40px; width: 420px; height: 190px;
    background: radial-gradient(ellipse at 50% 50%, var(--map-dark) 0%, rgba(53,53,56,0) 70%);
  }
  .card--dark .wordmark {
    position: relative; margin-top: 34px;
    font-size: 38px; font-weight: 700; letter-spacing: 4px; color: var(--brand-blue-bright);
  }
  .rule-caption {
    position: relative; display: flex; align-items: center; justify-content: center; gap: 12px;
    margin-top: 4px; font-size: 17px; letter-spacing: 8px; color: var(--rule-grey);
  }
  .rule-caption::before, .rule-caption::after {
    content: ""; width: 120px; height: 1px; background: var(--rule-grey);
  }
  .services {
    position: relative; margin-top: 16px; list-style: none;
    color: var(--brand-blue-bright); font-size: 15px; font-weight: 700; line-height: 25px;
  }
  .services .sep { color: var(--rule-grey); margin: 0 7px; }
  .address {
    position: relative; margin-top: 20px; color: var(--text-light);
    font-size: 15px; font-weight: 900;
  }
  .site {
    position: relative; margin-top: 2px; display: flex; align-items: center; justify-content: center; gap: 12px;
    color: var(--text-light); font-size: 15px; font-weight: 900;
  }
  .site::before, .site::after { content: ""; width: 70px; height: 1px; background: var(--rule-grey); }
  .site .accent { color: var(--brand-blue-bright); }
</style>
</head>
<body>
<main class="stage">

  <section class="card card--light" aria-label="Personal side of the business card">
    <div class="world-map" role="img" aria-label="Faint dotted world map in the background"></div>
    <div class="wordmark">QUILLSTONE CHIEF</div>
    <div class="identity">
      <p class="name">Dorian Pelletta</p>
      <p class="title">The Quillstone Chief</p>
    </div>
    <div class="divider"></div>
    <ul class="contacts">
      <li>
        <svg viewBox="0 0 24 24" aria-hidden="true"><path d="M6.6 10.8a15.2 15.2 0 0 0 6.6 6.6l2.2-2.2a1 1 0 0 1 1-.25 11.4 11.4 0 0 0 3.6.57 1 1 0 0 1 1 1V20a1 1 0 0 1-1 1A17 17 0 0 1 3 4a1 1 0 0 1 1-1h3.5a1 1 0 0 1 1 1c0 1.25.2 2.45.57 3.57a1 1 0 0 1-.25 1z"/></svg>
        619-555-0148
      </li>
      <li>
        <svg viewBox="0 0 24 24" aria-hidden="true"><path d="M2 5h20v14H2zm2 2v.5l8 5 8-5V7zm0 2.8V17h16V9.8l-8 5z"/></svg>
        Dorian@QuillstoneChief.example
      </li>
      <li>
        <svg viewBox="0 0 24 24" aria-hidden="true"><path d="M10.6 13.4a1 1 0 0 1 0-1.4l3.5-3.5a1 1 0 1 1 1.4 1.4L12 13.4a1 1 0 0 1-1.4 0zM8 20a4 4 0 0 1-2.8-6.8l2.5-2.5 1.4 1.4-2.5 2.5a2 2 0 0 0 2.8 2.8l2.5-2.5 1.4 1.4-2.5 2.5A4 4 0 0 1 8 20zm8.3-6.7-1.4-1.4 2.5-2.5a2 2 0 0 0-2.8-2.8l-2.5 2.5-1.4-1.4 2.5-2.5a4 4 0 0 1 5.6 5.6z"/></svg>
        www.QuillstoneChief.example
      </li>
    </ul>
    <p class="quote-band">The Fastest Way To Success Is To Take Action</p>
  </section>

  <section class="card card--dark" aria-label="Company side of the business card">
    <div class="world-map" role="img" aria-label="Faint dotted world map in the background"></div>
    <div class="wordmark">BRIGHTVALE</div>
    <p class="rule-caption">MEDIA</p>
    <ul class="services">
      <li>Advanced Website<span class="sep">•</span>App Development<span class="sep">•</span>Websites<span class="sep">•</span>Apps</li>
      <li>Online Voucher Systems<span class="sep">•</span>Leading Edge Marketing Services</li>
      <li>SMS<span class="sep">•</span>VB<span class="sep">•</span>SMM<span class="sep">•</span>SEM,</li>
    </ul>
    <p class="address">248 N. Larkmoor, 3rd Floor, San Diego CA 92173</p>
    <p class="site"><span>www.<span class="accent">BrightvaleMedia</span>.com</span></p>
  </section>

</main>
</body>
</html>
```